We need a business card for our gym. We are a PowerCore affiliate in Decatur Georgie established 2008. Our company name is Rally Functional Fitness. PowerCore Building Prime Fitness. Instagram and website is @rallygym. Hashtags we use #rallywithheart #madetorally We want something similar to the the black and neon green design attached but a different color scheme. No neon colors. Are company colors are the same as the blue and white card attached. We are open to ideas as far as colors however - just no neon.

Contact Information for Business Card

Rally Functional Fitness
472 Halvern Drive
Alderbrook GA 30041
Phone 404.555.0187 Website www.rallygym.example

Font styles to use
Other font styles liked:
• Futura Extra Bold Condensed

Colors

Designer to choose colors to be used in the design.

Requirements
Must have
• Our primary font we typically use for our name is Futura Extra Bold Condensed
Nice to have
• I attached a card from that is black and neon green from Zorva that we would like something similar. The blue and white is more similar to our colors. We also use have used black and white in the past. We use the chevrons as out logo. We are a PowerCore affiliate so I included a logo from them as well that may or may not be used on the card. Our instagram is @rallygym hashtags #madetorally #rallywithheart
Should not have
• No neon colors

```html
<!DOCTYPE html>
<html lang="en">
<head>
<meta charset="utf-8">
<title>Rally Functional Fitness — Business Card</title>
<link href="https://fonts.googleapis.com/css2?family=Archivo+Black&family=Oswald:wght@700&family=Montserrat:wght@400;500&display=swap" rel="stylesheet">
<style>
  :root {
    --backdrop: #2b2b2b;
    --card: #252525;
    --card-edge: #1d1d1d;
    --sky: #8fd0f2;
    --white: #ffffff;
    --soft-white: #e9e9e9;
    --rule: #9a9a9a;
  }
  * { box-sizing: border-box; margin: 0; padding: 0; }
  html, body {
    width: 1200px; height: 901px; overflow: hidden;
    background: var(--backdrop);
  }
  .sheet {
    position: relative; width: 1200px; height: 901px;
    display: flex; flex-direction: column; align-items: center; justify-content: center;
    gap: 44px;
  }
  .card {
    position: relative;
    width: 620px; height: 354px;
    background: var(--card);
    border: 1px solid var(--card-edge);
    box-shadow: 0 18px 40px rgba(0,0,0,.45);
    overflow: hidden;
  }
  .card-front .backdrop-shade {
    position: absolute; inset: 0;
    background: linear-gradient(110deg, #252525 0%, #2c2c2c 55%, #262626 100%);
  }
  .wordmark { text-transform: uppercase; line-height: 1; }
  .wordmark .brand {
    display: block;
    font-family: "Archivo Black", sans-serif; font-weight: 400;
    color: var(--sky); letter-spacing: -0.01em;
  }
  .wordmark .tagline {
    display: block;
    font-family: "Archivo Black", sans-serif; font-weight: 400;
    color: var(--white); letter-spacing: 0.01em;
  }
  .card-front .wordmark {
    position: absolute; left: 0; right: 0; top: 92px; text-align: center;
  }
  .card-front .brand { font-size: 104px; }
  .card-front .tagline { font-size: 33px; margin-top: 8px; }

  .card-back .wordmark {
    position: absolute; left: 40px; top: 120px; width: 260px; text-align: center;
  }
  .card-back .brand { font-size: 66px; }
  .card-back .tagline { font-size: 21px; margin-top: 6px; }

  .divider {
    position: absolute; left: 318px; top: 86px; width: 1px; height: 190px;
    background: var(--rule);
  }
  .contact {
    position: absolute; left: 346px; top: 92px;
    font-family: "Montserrat", sans-serif; color: var(--soft-white);
  }
  .contact .person {
    font-family: "Oswald", sans-serif; font-weight: 700;
    color: var(--sky); font-size: 26px; letter-spacing: 0.06em;
    word-spacing: 0.3em; text-transform: uppercase; line-height: 1;
  }
  .contact .role { font-size: 15px; letter-spacing: 0.06em; margin-top: 6px; }
  .contact .address { font-size: 16px; line-height: 1.35; margin-top: 16px; letter-spacing: 0.02em; }
  .contact .line {
    display: flex; align-items: center; gap: 8px;
    font-size: 16px; letter-spacing: 0.02em; margin-top: 10px;
  }
  .contact .line + .line { margin-top: 4px; }
  .contact svg { width: 14px; height: 14px; flex: none; }
</style>
</head>
<body>
<main class="sheet">

  <section class="card card-front" aria-label="Card front">
    <div class="backdrop-shade" role="img" aria-label="Soft dark background where faint brand chevrons belong"></div>
    <h1 class="wordmark">
      <span class="brand">Rally</span>
      <span class="tagline">Functional Fitness</span>
    </h1>
  </section>

  <section class="card card-back" aria-label="Card back">
    <div class="wordmark">
      <span class="brand">Rally</span>
      <span class="tagline">Functional Fitness</span>
    </div>
    <div class="divider"></div>
    <div class="contact">
      <p class="person">Marcus Whitfield</p>
      <p class="role">EXPERT COACHES</p>
      <p class="address">472 Halvern Drive<br>Alderbrook GA 30041</p>
      <p class="line">
        <svg viewBox="0 0 24 24" aria-hidden="true"><path fill="#8fd0f2" d="M6.6 10.8a15.1 15.1 0 0 0 6.6 6.6l2.2-2.2a1 1 0 0 1 1-.25 11.4 11.4 0 0 0 3.6.57 1 1 0 0 1 1 1V20a1 1 0 0 1-1 1A17 17 0 0 1 3 4a1 1 0 0 1 1-1h3.5a1 1 0 0 1 1 1c0 1.25.2 2.45.57 3.57a1 1 0 0 1-.25 1z"/></svg>
        404.555.0187
      </p>
      <p class="line">
        <svg viewBox="0 0 24 24" aria-hidden="true"><g fill="none" stroke="#8fd0f2" stroke-width="2"><circle cx="12" cy="12" r="9"/><path d="M3 12h18M12 3c3 3 3 15 0 18M12 3c-3 3-3 15 0 18"/></g></svg>
        www.rallygym.example
      </p>
    </div>
  </section>

</main>
</body>
</html>
```